HarborQuote - Webstartup looking for some style

HarborQuote is a cloud based web application that allows construction sub-contractors to create and manage bids. Generally, these contractors will contact subcontractors to have them do specific parts of a larger construction project. This would be used by various subcontractors including woodwork (cabinetry), electricians, masons, etc...

Nearly all competitors are clients applications that have to be installed on the computer and are very expensive. This is a much lower cost alternative.

The business is just beginning and we want people to view us as a fresh alternative to companies that have been around for a long time and are starting to look a little dated.

We would like our logo included on the card (see attached). We have been using the circular 'hq' emblem seperately from the complete logo in various areas of the website. We lean towards a professional and clean look, with a tendancy more towards modern.

We want to differentiate ourselves from our competition which tend to be dated, complicated and less graphical.

(We are currently designing our public website as well - but don't have any designs yet)

Industry/Entity Type

Construction

Requirements
Must have
• Circular 'hq' emblem from logo. Probably entire logo, but not necessarily.

Should have reference to website: www.harborquote-example.com

The Url should be all lowercase (www.harborquote-example.com)
Should not have
• we do not want to list a phone number or email address on the cards. we want people to go to the actual website. we haven't decided if we want names printed on the business cards.

```html
<!DOCTYPE html>
<html lang="en">
<head>
<meta charset="utf-8">
<title>HarborQuote Business Card</title>
<link href="https://fonts.googleapis.com/css2?family=Arimo:wght@400&family=Roboto+Condensed:wght@700&display=swap" rel="stylesheet">
<style>
  :root {
    --backdrop: #e4e6e9;
    --card: #ffffff;
    --card-edge: #f1f2f4;
    --brand-blue: #1f6fba;
    --ink: #1d1d1f;
  }
  * { margin: 0; padding: 0; box-sizing: border-box; }
  html, body {
    width: 1200px;
    height: 900px;
    overflow: hidden;
    background: var(--backdrop);
  }
  .stage {
    width: 1200px;
    height: 900px;
    display: flex;
    align-items: center;
    justify-content: center;
  }
  .business-card {
    position: relative;
    width: 900px;
    height: 514px;
    background: linear-gradient(180deg, var(--card) 0%, var(--card-edge) 100%);
    border-radius: 28px;
    box-shadow: 0 6px 24px rgba(0, 0, 0, 0.12);
  }
  .brand {
    position: absolute;
    left: 0;
    right: 0;
    top: 150px;
    display: flex;
    justify-content: center;
    align-items: center;
    gap: 22px;
  }
  .brand-emblem {
    width: 118px;
    height: 118px;
    flex: none;
  }
  .brand-text {
    display: flex;
    flex-direction: column;
    align-items: flex-end;
  }
  .brand-name {
    font-family: "Arimo", Arial, sans-serif;
    font-weight: 400;
    font-size: 80px;
    line-height: 1;
    letter-spacing: -1px;
    color: var(--brand-blue);
  }
  .brand-tagline {
    margin-top: 8px;
    font-family: "Roboto Condensed", "Arial Narrow", sans-serif;
    font-weight: 700;
    font-size: 25px;
    letter-spacing: -0.3px;
    white-space: nowrap;
    color: var(--ink);
  }
  .website {
    position: absolute;
    left: 0;
    right: 0;
    top: 384px;
    text-align: center;
    font-family: "Arimo", Arial, sans-serif;
    font-weight: 400;
    font-size: 44px;
    color: var(--brand-blue);
  }
</style>
</head>
<body>
  <main class="stage">
    <section class="business-card" aria-label="HarborQuote business card">
      <div class="brand">
        <svg class="brand-emblem" viewBox="0 0 118 118" aria-hidden="true">
          <circle cx="59" cy="59" r="57" fill="var(--brand-blue)"/>
        </svg>
        <div class="brand-text">
          <span class="brand-name">HarborQuote</span>
          <span class="brand-tagline">Streamlining Trade Contractor Quotes</span>
        </div>
      </div>
      <p class="website">www.harborquote-example.com</p>
    </section>
  </main>
</body>
</html>
```